** Wanted ** Wordpress web design for scaffolding rental and construction company

We need a website design and must be functional to show a basic overview of what our company offers as a service. We have a domain name and a logo but we need web design. This web site should have another scaffolding rental page for construction and renovation as well as a quote section where customers can enter their personal information and also upload photos. The site% 26quot; www.brindlework.com% 26quot; should be intuitive, clear and classy ... The logo must be found on the site in several ways.

Target Market(s)

Professional and no professional

Coding

Coded - Design and coding required

Number of Pages Required

3 page

Font styles to use
Serif
Sans Serif
Decorative
Script

Requirements
Must have
• Our logo
Nice to have
• Slogan:% 26quot; The height% 26 # 224; port% 26 # 233; e hand% 26quot;

```html
<!DOCTYPE html>
<html lang="en">
<head>
<meta charset="utf-8">
<title>Brindlework – Scaffolding &amp; Construction</title>
<link rel="stylesheet" href="https://fonts.googleapis.com/css2?family=Jost:wght@400;500;600&family=Lato:wght@400;700&display=swap">
<style>
:root{
  --orange:#ef8a1e;
  --ink:#111111;
  --body:#6d6d6d;
  --ghost:#efefef;
  --navy:#0f1a33;
  --card-line:#f1e6da;
}
*{box-sizing:border-box;margin:0;padding:0}
html,body{width:1200px;height:3953px;overflow:hidden;background:#fff}
body{position:relative;font-family:'Lato',sans-serif;color:var(--body)}
.abs{position:absolute}
h1,h2,h3{font-family:'Jost',sans-serif;color:var(--ink);font-weight:500}
.btn{position:absolute;background:var(--orange);color:#fff;border-radius:30px;display:flex;align-items:center;justify-content:center;font-family:'Jost',sans-serif;font-weight:500}
.brand{position:absolute;display:flex;align-items:center;gap:10px;font-family:'Jost',sans-serif;font-weight:600;color:var(--orange);letter-spacing:2px}
.brand-square{width:22px;height:22px;background:var(--orange)}
.ghost-word{position:absolute;font-family:'Jost',sans-serif;font-weight:500;font-size:78px;color:var(--ghost);writing-mode:vertical-rl;transform:rotate(180deg);letter-spacing:2px;line-height:1}
.ghost-word.right{transform:rotate(180deg)}
.center{text-align:center;left:0;width:1200px}
.sub{font-size:12px;line-height:20px;color:var(--body)}
.photo{position:absolute}
.card{position:absolute;top:1194px;width:229px;height:191px;background:#fff;border:2px solid var(--card-line);border-radius:6px;box-shadow:0 2px 8px rgba(0,0,0,.05);text-align:center}
.card-icon{position:absolute;left:84px;top:-32px;width:60px;height:60px;border-radius:50%;background:#fff;border:2px solid var(--orange);display:flex;align-items:center;justify-content:center}
.card h3{margin-top:48px;font-size:16px}
.card p{margin:12px 16px 0;font-size:11px;line-height:20px}
.dot{position:absolute;left:53px;width:10px;height:10px;border:1.5px solid var(--orange);transform:rotate(45deg)}
.dot.on{background:var(--orange)}
.footer-nav{position:absolute;top:3632px;left:0;width:1200px;display:flex;justify-content:center;gap:22px;color:#fff;font-size:12px}
.contact{position:absolute;top:3692px;width:200px;text-align:center;color:#fff;font-size:11px;line-height:19px}
.contact-icon{width:48px;height:48px;margin:0 auto 14px;border-radius:50%;background:#fff;display:flex;align-items:center;justify-content:center}
.social{position:absolute;top:3827px;width:36px;height:36px;border-radius:50%;border:2px solid var(--orange)}
.social.on{background:var(--orange)}
</style>
</head>
<body>

<!-- Header -->
<div class="brand" style="left:161px;top:42px;font-size:24px"><span class="brand-square"></span>BRINDLEWORK</div>

<svg class="abs" style="left:0;top:0" width="1200" height="600" viewBox="0 0 1200 600">
  <defs>
    <linearGradient id="heroSky" x1="0" y1="0" x2="1" y2="1">
      <stop offset="0" stop-color="#27407a"/>
      <stop offset=".55" stop-color="#6f87a8"/>
      <stop offset="1" stop-color="#b7c23a"/>
    </linearGradient>
  </defs>
  <ellipse cx="1090" cy="110" rx="494" ry="450" fill="var(--orange)"/>
  <ellipse cx="1110" cy="100" rx="498" ry="455" fill="url(#heroSky)" role="img" aria-label="Workers in hard hats looking up at tall buildings"/>
  <g stroke="#fff" stroke-width="3"><line x1="916" y1="52" x2="958" y2="52"/><line x1="916" y1="63" x2="958" y2="63"/><line x1="916" y1="74" x2="958" y2="74"/></g>
  <circle cx="1018" cy="63" r="20" fill="var(--orange)"/>
  <circle cx="1018" cy="57" r="5" fill="#fff"/><path d="M1009 72a9 8 0 0 1 18 0z" fill="#fff"/>
  <circle cx="947" cy="559" r="27" fill="var(--orange)" stroke="#fff" stroke-width="3"/>
  <path d="M942 550l12 9-12 9z" fill="#fff"/>
</svg>

<div class="dot" style="top:229px"></div>
<div class="dot" style="top:264px"></div>
<div class="dot on" style="top:299px"></div>
<div class="dot" style="top:334px"></div>

<h1 class="abs" style="left:162px;top:232px;font-size:50px;font-weight:600">The Height, Port</h1>
<p class="abs" style="left:163px;top:302px;width:380px;font-size:12.5px;line-height:23px">Lorem Ipsum is simply dummy text of the printing and typesetting industry. Lorem Ipsum has been the industry's standard dummy text ever since the 1500s</p>
<div class="btn" style="left:161px;top:399px;width:172px;height:50px;font-size:18px">Get In Touch</div>

<!-- About -->
<div class="ghost-word" style="left:2px;top:612px;height:380px">ABOUT US</div>
<div class="photo" role="img" aria-label="Modern glass and timber house" style="left:196px;top:600px;width:274px;height:274px;border-radius:50%;background:linear-gradient(135deg,#2a6fd1,#7fb0e6 55%,#3a3a3a);border:8px solid #fff;box-shadow:0 4px 14px rgba(0,0,0,.12)"></div>
<div class="photo" role="img" aria-label="Construction worker on a building site" style="left:355px;top:757px;width:190px;height:190px;border-radius:50%;background:linear-gradient(180deg,#a8c6e6,#d8d2c6 60%,#8b7a62);border:8px solid #fff;box-shadow:0 4px 14px rgba(0,0,0,.12)"></div>
<div class="abs" style="left:497px;top:699px;width:44px;height:44px;border-radius:50%;background:var(--orange)"></div>
<div class="abs" style="left:311px;top:909px;width:29px;height:29px;border-radius:50%;border:1.5px solid var(--orange)"></div>

<h2 class="abs" style="left:613px;top:640px;font-size:35px">About Us</h2>
<p class="abs" style="left:612px;top:700px;width:380px;font-size:11px;line-height:19.5px">Lorem Ipsum is simply dummy text of the printing and typesetting industry. Lorem Ipsum has been the industry's standard dummy text ever since the 1500s, when an unknown printer took a galley of type and scrambled it to make a type specimen book. It has survived not only five centuries, but also the leap into electronic typesetting, remaining essentially unchanged.</p>
<p class="abs" style="left:612px;top:816px;width:380px;font-size:11px;line-height:19.5px">It was popularised in the 1960s with the release of Letraset sheets containing Lorem Ipsum passages.</p>
<div class="btn" style="left:611px;top:901px;width:120px;height:35px;font-size:13px">Read More</div>

<!-- Services -->
<div class="ghost-word right" style="left:1126px;top:1036px;height:355px">SERVICES</div>
<h2 class="abs center" style="top:1044px;font-size:34px">What We Provide?</h2>
<p class="abs center sub" style="top:1089px">Lorem Ipsum is simply dummy text of the printing and typesetting industry. Lorem<br>Ipsum has been the industry's standard dummy text.</p>

<div class="card" style="left:230px">
  <div class="card-icon"><svg width="30" height="30" viewBox="0 0 30 30" fill="none" stroke="var(--orange)" stroke-width="1.6"><rect x="5" y="4" width="20" height="22"/><line x1="5" y1="11" x2="25" y2="11"/><line x1="5" y1="19" x2="25" y2="19"/><line x1="5" y1="11" x2="25" y2="19"/></svg></div>
  <h3>Scaffolding</h3>
  <p>Lorem Ipsum is simply dummy text of the printing and typesetting industry. Lorem Ipsum has been the industry's standard dummy text ever since the 1500s.</p>
</div>
<div class="card" style="left:485px">
  <div class="card-icon"><svg width="30" height="30" viewBox="0 0 30 30" fill="none" stroke="var(--orange)" stroke-width="1.6"><rect x="4" y="5" width="22" height="15"/><line x1="15" y1="20" x2="15" y2="26"/><line x1="9" y1="26" x2="21" y2="26"/><path d="M9 16l4-4 3 3 5-5"/></svg></div>
  <h3>Elevation</h3>
  <p>Lorem Ipsum is simply dummy text of the printing and typesetting industry. Lorem Ipsum has been the industry's standard dummy text ever since the 1500s.</p>
</div>
<div class="card" style="left:740px">
  <div class="card-icon"><svg width="30" height="30" viewBox="0 0 30 30" fill="none" stroke="var(--orange)" stroke-width="1.6"><path d="M4 14L15 5l11 9"/><path d="M7 12v13h16V12"/><rect x="12" y="16" width="6" height="9"/></svg></div>
  <h3>Renovation</h3>
  <p>Lorem Ipsum is simply dummy text of the printing and typesetting industry. Lorem Ipsum has been the industry's standard dummy text ever since the 1500s.</p>
</div>
<div class="btn" style="left:540px;top:1444px;width:120px;height:37px;font-size:13px">Read More</div>

<!-- Projects -->
<h2 class="abs" style="left:163px;top:1574px;font-size:34px">Our Projects</h2>
<p class="abs sub" style="left:163px;top:1625px;width:340px">Lorem Ipsum is simply dummy text of the printing and typesetting industry. Lorem Ipsum has been the industry's standard dummy text.</p>
<svg class="abs" style="left:830px;top:1604px" width="72" height="34" viewBox="0 0 72 34">
  <circle cx="17" cy="17" r="15" fill="#ededed"/><path d="M20 11l-6 6 6 6" stroke="#777" stroke-width="1.6" fill="none"/>
  <circle cx="55" cy="17" r="15" fill="#ededed"/><path d="M52 11l6 6-6 6" stroke="#777" stroke-width="1.6" fill="none"/>
</svg>
<div class="ghost-word" style="left:2px;top:1952px;height:360px">PROJECTS</div>

<div class="photo" role="img" aria-label="Timber frame house under construction with crane" style="left:161px;top:1725px;width:278px;height:188px;background:linear-gradient(180deg,#7ea7d8,#4f7a52 60%,#a08d6c)"></div>
<div class="photo" role="img" aria-label="Curved glass facade of a tower" style="left:460px;top:1730px;width:277px;height:397px;background:linear-gradient(135deg,#c8d6e8,#8ea3bd 50%,#d6dde6)"></div>
<div class="photo" role="img" aria-label="Scaffolding structure at dusk" style="left:761px;top:1725px;width:278px;height:188px;background:linear-gradient(180deg,#5b86c9,#b8bfd6 75%,#cfc3c9)"></div>
<div class="photo" role="img" aria-label="High-rise under construction beneath cloudy sky" style="left:161px;top:1936px;width:278px;height:187px;background:linear-gradient(180deg,#3c4a5a,#8b96a2 60%,#c3c8cc)"></div>
<div class="photo" role="img" aria-label="Tower with stacked balconies" style="left:761px;top:1936px;width:278px;height:397px;background:linear-gradient(135deg,#d9b9a3,#a7b0d0 60%,#5f5a57)"></div>
<div class="photo" role="img" aria-label="Red brick building against blue sky" style="left:161px;top:2146px;width:577px;height:396px;background:linear-gradient(180deg,#b9d6ea,#7bb6d8 45%,#a9493a 75%,#7a3328)"></div>
<div class="photo" role="img" aria-label="Interior under renovation with windows" style="left:761px;top:2356px;width:278px;height:186px;background:linear-gradient(180deg,#8c7a52,#d8c99f 55%,#a8956b)"></div>

<!-- Testimonials -->
<div class="ghost-word right" style="left:1126px;top:2668px;height:305px">CLIENTS</div>
<h2 class="abs center" style="top:2614px;font-size:34px">Our Testimonials</h2>
<p class="abs center sub" style="top:2658px">Lorem Ipsum is simply dummy text of the printing and typesetting industry. Lorem<br>Ipsum has been the industry's standard dummy text.</p>
<div class="abs" style="left:385px;top:2742px;width:429px;height:187px;background:var(--orange);box-shadow:0 4px 12px rgba(0,0,0,.1)"></div>
<div class="abs" style="left:576px;top:2748px;font-family:'Jost',sans-serif;font-size:80px;line-height:80px;color:#f6b36b;font-weight:600">&ldquo;</div>
<p class="abs" style="left:415px;top:2806px;width:370px;text-align:center;color:#fff;font-size:11px;line-height:19.5px">Lorem Ipsum is simply dummy text of the printing and typesetting industry. Lorem Ipsum has been the industry's standard dummy text ever since the 1500s.</p>
<div class="photo" role="img" aria-label="Client portrait" style="left:560px;top:2887px;width:74px;height:74px;border-radius:50%;background:linear-gradient(180deg,#6a6a6a,#c9c2bb);border:3px solid #fff;box-shadow:0 2px 6px rgba(0,0,0,.2)"></div>
<p class="abs center" style="top:2981px;font-size:13px;color:var(--ink)">-Client Name</p>

<!-- Newsletter -->
<h2 class="abs center" style="top:3139px;font-size:34px">Our Newsletter</h2>
<p class="abs center sub" style="top:3183px">Lorem Ipsum is simply dummy text of the printing and typesetting industry. Lorem<br>Ipsum has been the industry's standard dummy text.</p>
<div class="abs" style="left:431px;top:3250px;width:338px;height:40px;border-radius:22px;background:#f2f2f2;border:1px solid #ddd;padding-left:20px;display:flex;align-items:center;font-size:11px;color:#888">Enter Email:</div>
<div class="btn" style="left:533px;top:3310px;width:135px;height:35px;font-size:13px">Subscribe Now</div>

<!-- Footer -->
<svg class="abs" style="left:0;top:3350px" width="1200" height="603" viewBox="0 0 1200 603">
  <defs>
    <linearGradient id="footerShade" x1="0" y1="0" x2="0" y2="1">
      <stop offset="0" stop-color="#0b1430"/>
      <stop offset=".6" stop-color="#1b2445"/>
      <stop offset="1" stop-color="#2a2a36"/>
    </linearGradient>
  </defs>
  <path role="img" aria-label="Building under construction at night" d="M0 110 C80 60 180 0 280 20 C400 45 480 100 600 85 C720 70 820 10 960 15 C1060 20 1140 70 1200 110 L1200 603 L0 603Z" fill="url(#footerShade)"/>
  <rect x="0" y="560" width="1200" height="43" fill="var(--orange)"/>
  <line x1="426" y1="366" x2="573" y2="366" stroke="#aaa" stroke-dasharray="2 3"/>
  <line x1="621" y1="366" x2="768" y2="366" stroke="#aaa" stroke-dasharray="2 3"/>
</svg>

<div class="brand" style="left:0;width:1200px;justify-content:center;top:3552px;font-size:30px"><span class="brand-square" style="width:26px;height:26px"></span>BRINDLEWORK</div>

<nav class="footer-nav"><span>Home</span><span>About Us</span><span>Services</span><span>Testimonials</span><span>Gallery</span><span>Contact Us</span></nav>

<div class="contact" style="left:302px">
  <div class="contact-icon"><svg width="22" height="22" viewBox="0 0 22 22"><path d="M11 2a7 7 0 0 0-7 7c0 5 7 11 7 11s7-6 7-11a7 7 0 0 0-7-7z" fill="var(--orange)"/><circle cx="11" cy="9" r="2.6" fill="#fff"/></svg></div>
  100 Lorem ipsum is simply<br>dummy text
</div>
<div class="contact" style="left:497px">
  <div class="contact-icon"><svg width="22" height="22" viewBox="0 0 22 22"><path d="M5 3l4 0 1.5 4-2.3 1.6a11 11 0 0 0 5.2 5.2L15 11.5l4 1.5v4c0 1-1 2-2 2A15 15 0 0 1 3 5c0-1 1-2 2-2z" fill="var(--orange)"/></svg></div>
  Call us on:<br>+91-000-000-0000
</div>
<div class="contact" style="left:692px">
  <div class="contact-icon"><svg width="22" height="22" viewBox="0 0 22 22"><rect x="3" y="5" width="16" height="12" rx="1.5" fill="var(--orange)"/><path d="M3.5 6l7.5 6 7.5-6" stroke="#fff" stroke-width="1.4" fill="none"/></svg></div>
  Email<br>info@brindlework.com
</div>

<div class="social" style="left:515px" aria-label="Social profile one"></div>
<div class="social on" style="left:559px" aria-label="Social profile two"></div>
<div class="social" style="left:604px" aria-label="Social profile three"></div>
<div class="social" style="left:648px" aria-label="Social profile four"></div>

<p class="abs center" style="top:3924px;font-size:11px;color:#fff">Copyright © 2020 Brindlework. All Rights Reserved. Terms &amp; Conditions | Privacy Policy</p>

</body>
</html>
```